Business Card design for law firm = Brightvale Australia

We are seeking a new design for our business cards.
We are keeping our logo, which is attached.
We need space for
Name
Title
Address is , which is
Level 7
214 Marlowe Street
Sydney NSW 2047
Phone :
Mobile :
Fax :
Email :
DX :
website www.brightvale-example.com.au

Industry/Entity Type

Law Firm / Banking and Finance

Contact Information for Business Card

We are seeking a new design for our business cards. We are keeping our logo. We need space for Name Title Address is Level 7 214 Marlowe Street Sydney NSW 2047 Phone Mobile Fax Email DX website www.brightvale-example.com.au

Colors
0054AA
0677BA
7BADD7
CADEEF
E8F1F8

Requirements
Must have
• see our website for general feel www.brightvale-example.com.au

```html
<!DOCTYPE html>
<html lang="en">
<head>
<meta charset="utf-8">
<title>Brightvale Australia – Business Card</title>
<link rel="stylesheet" href="https://fonts.googleapis.com/css2?family=Source+Sans+3:wght@400;600&display=swap">
<style>
  :root {
    --brand-navy: #0054AA;
    --brand-blue: #0677BA;
    --brand-sky: #7BADD7;
    --brand-mist: #CADEEF;
    --brand-ice: #E8F1F8;
    --ink: #3a3a3a;
    --ink-soft: #5a5a5a;
    --stage: #ecedef;
    --card-white: #ffffff;
    --card-grey-a: #f2f2f3;
    --card-grey-b: #d9dadc;
  }
  * { box-sizing: border-box; margin: 0; padding: 0; }
  html, body { width: 1200px; height: 900px; overflow: hidden; }
  body {
    background: var(--stage);
    font-family: "Source Sans 3", Arial, sans-serif;
    color: var(--ink);
    position: relative;
  }
  .card {
    position: absolute;
    left: 300px;
    width: 600px;
    height: 366px;
    box-shadow: 0 8px 24px rgba(0,0,0,.18);
  }
  .card--back {
    top: 56px;
    background: linear-gradient(160deg, var(--card-grey-a), var(--card-grey-b));
  }
  .card--front {
    top: 478px;
    background: var(--card-white);
  }

  /* Brand lockup: name with a small dot beside it */
  .brand {
    position: absolute;
    display: flex;
    align-items: center;
    gap: 12px;
  }
  .brand__dot {
    flex: none;
    width: 14px;
    height: 14px;
    border-radius: 50%;
    background: var(--brand-sky);
  }
  .brand__name {
    font-weight: 400;
    font-size: 40px;
    line-height: 1;
    color: var(--brand-navy);
    letter-spacing: .5px;
  }
  .card--back .brand { left: 0; right: 0; top: 160px; justify-content: center; }
  .card--front .brand { left: 0; width: 434px; top: 78px; justify-content: center; }

  .rule {
    position: absolute;
    left: 24px;
    top: 152px;
    width: 410px;
    height: 1px;
    background: var(--brand-blue);
  }

  .person {
    position: absolute;
    right: 24px;
    top: 128px;
    text-align: right;
  }
  .person__name { font-size: 18px; font-weight: 600; color: var(--brand-blue); line-height: 1.2; }
  .person__title { font-size: 13px; color: var(--ink-soft); }

  .address {
    position: absolute;
    right: 24px;
    top: 192px;
    text-align: right;
    font-size: 14px;
    font-style: normal;
    line-height: 1.4;
    color: var(--ink-soft);
  }
  .address__label { color: var(--brand-navy); font-weight: 600; }

  .contacts {
    position: absolute;
    left: 24px;
    top: 232px;
    list-style: none;
    font-size: 15px;
    line-height: 1.35;
    color: var(--ink);
  }
  .contacts__gap { margin-top: 8px; }
  .contacts__label {
    display: inline-block;
    width: 22px;
    font-weight: 600;
    color: var(--brand-navy);
  }
</style>
</head>
<body>
  <section class="card card--back" aria-label="Card back">
    <div class="brand">
      <span class="brand__dot"></span>
      <span class="brand__name">Brightvale</span>
    </div>
  </section>

  <section class="card card--front" aria-label="Card front">
    <div class="brand">
      <span class="brand__dot"></span>
      <span class="brand__name">Brightvale</span>
    </div>

    <div class="rule"></div>

    <div class="person">
      <p class="person__name">Sam Whitford</p>
      <p class="person__title">Managing Director</p>
    </div>

    <address class="address">
      Level 7, 214 Marlowe Street<br>
      Sydney NSW 2047<br>
      <span class="address__label">DX</span> 318 Sydney
    </address>

    <ul class="contacts">
      <li><span class="contacts__label">M.</span>04 5550 1182</li>
      <li><span class="contacts__label">T.</span>02 5550 0147</li>
      <li><span class="contacts__label">F.</span>02 5550 6390</li>
      <li class="contacts__gap"><span class="contacts__label">E.</span>enquiries@brightvale-example.com.au</li>
      <li><span class="contacts__label">W.</span>www.brightvale-example.com.au</li>
    </ul>
  </section>
</body>
</html>
```